I need a logo that demonstrates multiple of the same with one of a distinguishing feature. I would like something that can be recognisable in silhouette format. The business designs Management systems bespoke the to the company helping them pre-qualify for work.
Something that can demonstrate a distinction between a collective group non of which are the same in shape or size, with the largest of these not the distinguished object (or something to that effect).
This is a new business no logo or artwork exists.
Target Market(s)
Small to Medium Size enterprises in the city and rural areas. Looking to make the step up.
Industry/Entity Type
Manufacture
Contact Information for Business Card
room for, Name, Email, phone number
Font styles to use
Requirements
Must have
- would like the silhouette to be recognisable
Nice to have
- would like it to incorporate the name Keystone Advisory Frameworks.
- Would like the same logo to be on both business cards and on corporate shirts
Should not have
- anything that may exclude rural trade or manufacturing.
- I don't want to appear as corporate, just professional

```html
<!DOCTYPE html>
<html lang="en">
<head>
<meta charset="utf-8">
<title>Keystone Advisory Frameworks – Business Card</title>
<link rel="stylesheet" href="https://fonts.googleapis.com/css2?family=Source+Sans+3:wght@400;600&display=swap">
<style>
  :root {
    --bg: #3a302c;
    --card-dark: #1f1f21;
    --card-red: #e93a30;
    --brand-red: #e8262d;
    --text-light: #ecebeb;
    --divider: #5a2a2a;
    --white: #ffffff;
  }
  * { box-sizing: border-box; margin: 0; padding: 0; }
  html, body {
    width: 1200px; height: 844px; overflow: hidden;
    background: var(--bg);
    font-family: "Source Sans 3", Arial, sans-serif;
  }
  .canvas {
    position: relative; width: 1200px; height: 844px;
    display: flex; align-items: center; justify-content: center; gap: 40px;
  }
  .card {
    width: 520px; height: 300px; border-radius: 3px;
    position: relative; overflow: hidden;
    box-shadow: 0 10px 24px rgba(0,0,0,0.35);
  }
  .card-front { background: var(--card-dark); display: flex; }
  .brand-block {
    width: 250px; display: flex; flex-direction: column;
    align-items: center; justify-content: center; gap: 14px;
    padding: 40px 20px 0;
  }
  .brand-dot {
    width: 34px; height: 34px; border-radius: 50%;
    background: var(--brand-red);
  }
  .brand-name {
    color: var(--brand-red); font-weight: 600; font-size: 24px;
    line-height: 1.1; text-align: center;
  }
  .divider { width: 1px; margin: 60px 0; background: var(--divider); }
  .contact-block {
    flex: 1; padding: 58px 0 0 26px; color: var(--text-light);
    font-size: 14px; line-height: 1.35;
  }
  .person-name { color: var(--brand-red); font-weight: 600; font-size: 17px; }
  .person-role { margin-bottom: 16px; }
  .address { margin-bottom: 16px; }
  .contact-list { list-style: none; }
  .contact-list li { display: flex; align-items: center; gap: 9px; }
  .contact-list svg { width: 11px; height: 11px; fill: var(--brand-red); flex: none; }
  .card-back {
    background: var(--card-red);
    display: flex; flex-direction: column; align-items: center; justify-content: center; gap: 18px;
  }
  .back-dot { width: 48px; height: 48px; border-radius: 50%; background: var(--white); }
  .back-name {
    color: var(--white); font-weight: 600; font-size: 30px;
    text-align: center; line-height: 1.15;
  }
</style>
</head>
<body>
<main class="canvas">
  <section class="card card-front" aria-label="Business card front">
    <div class="brand-block">
      <span class="brand-dot"></span>
      <p class="brand-name">Keystone Advisory Frameworks</p>
    </div>
    <div class="divider"></div>
    <div class="contact-block">
      <p class="person-name">Daniel Harper</p>
      <p class="person-role">Managing Director</p>
      <p class="address">48 Millbrook Lane<br>Harrowfield, HF2 7QL.</p>
      <ul class="contact-list">
        <li><svg viewBox="0 0 12 12"><path d="M2.5 0.5 4.5 3 3.4 4.4c.7 1.6 2 2.9 3.6 3.6L8.4 6.9 11 9l-.9 2C5.4 11 .9 6.6 1 1.8z"/></svg>055-210 384 617</li>
        <li><svg viewBox="0 0 12 12"><path d="M0 2h12v8H0zM1 3l5 4 5-4v-.2H1z" fill-rule="evenodd"/></svg>hello@keystoneaf.com</li>
        <li><svg viewBox="0 0 12 12"><path d="M5 7 7 5M4.5 5.5 2.5 7.5a1.8 1.8 0 0 0 2.5 2.5l2-2M7.5 6.5l2-2A1.8 1.8 0 0 0 7 2L5 4" stroke="#e8262d" stroke-width="1.4" fill="none" stroke-linecap="round"/></svg>www.keystoneaf.com</li>
      </ul>
    </div>
  </section>
  <section class="card card-back" aria-label="Business card back">
    <span class="back-dot"></span>
    <p class="back-name">Keystone Advisory<br>Frameworks</p>
  </section>
</main>
</body>
</html>
```